Stationery Design Project

I need a stationary design for our company. we are based in Houston, TX and we are called Mira Vell Lending. And we are wanting to brand our MoneyMendPlus program, which includes our tax preparation and restoration, credit repair service. Although our business offers other programs, we are interested in mainly focusing on The MoneyMendPlus program. We are looking for way to brand our ourselves and I believe that a great stationery design will help in achieving this goal. Our logo design is blue and light blue. the slogan is orange.

Industry/Entity Type

Business

Requirements
Must have
• Address: 30871 Calloway Ln. B-22
Houston, TX 75419
Tel. 555-318-6207
Fax 555-294-7153
www.miravelllending.example
info@miravelllending.example
Our Slogan: Happiness, Restored!

```html
<!DOCTYPE html>
<html lang="en">
<head>
<meta charset="utf-8">
<title>MoneyMendPlus – Business Card</title>
<link rel="stylesheet" href="https://fonts.googleapis.com/css2?family=Tinos:wght@400;700&family=Didact+Gothic&display=swap">
<style>
  :root {
    --navy: #0f4f86;
    --blue: #1a6fae;
    --sky: #3b9bd6;
    --orange: #f39a1e;
    --white: #ffffff;
    --ink: #1d2a3a;
    --page: #e9ebee;
    --serif: "Tinos", "Times New Roman", serif;
    --sans: "Didact Gothic", "Century Gothic", sans-serif;
  }
  * { box-sizing: border-box; margin: 0; padding: 0; }
  html, body { width: 1200px; height: 724px; overflow: hidden; background: var(--page); }
  .stage { position: relative; width: 1200px; height: 724px; }

  .card {
    position: absolute;
    width: 540px; height: 310px;
    top: 207px;
    overflow: hidden;
    box-shadow: 0 6px 18px rgba(0,0,0,.18);
  }
  .card > svg { position: absolute; inset: 0; width: 100%; height: 100%; }

  /* Front */
  .card-front { left: 45px; background: var(--white); }
  .brand-front {
    position: absolute; left: 62px; top: 78px;
    display: flex; align-items: center; gap: 10px;
  }
  .brand-dot { width: 14px; height: 14px; border-radius: 50%; background: var(--orange); }
  .brand-front .brand-name {
    font-family: var(--serif); font-size: 44px; color: var(--blue); letter-spacing: -.5px;
  }
  .contact {
    position: absolute; left: 62px; top: 150px;
    font-family: var(--sans); font-size: 13.5px; color: var(--ink); line-height: 1.55;
    list-style: none;
  }
  .contact .address { margin-bottom: 6px; }
  .contact li { display: flex; align-items: center; gap: 7px; }
  .contact svg { width: 11px; height: 11px; fill: var(--blue); flex: none; }
  .slogan {
    position: absolute; right: 22px; bottom: 42px;
    font-family: var(--serif); font-weight: 700; font-size: 19px; line-height: 1.15;
    color: var(--white); text-align: center;
  }

  /* Back */
  .card-back {
    left: 615px;
    background: radial-gradient(circle at 55% 45%, var(--sky) 0%, var(--blue) 40%, var(--navy) 100%);
  }
  .back-frame {
    position: absolute; left: 168px; top: 40px; width: 205px; height: 215px;
    border: 6px solid rgba(255,255,255,.12); border-radius: 4px;
  }
  .brand-back {
    position: absolute; left: 0; right: 0; top: 108px; text-align: center;
    font-family: var(--serif); font-size: 56px; color: var(--white); letter-spacing: -.5px;
  }
  .back-company {
    position: absolute; left: 0; right: 0; top: 180px; text-align: center;
    font-family: var(--serif); font-weight: 700; font-size: 20px; color: rgba(255,255,255,.16);
  }
  .back-web {
    position: absolute; left: 0; right: 0; top: 218px; text-align: center;
    font-family: var(--serif); font-size: 13px; letter-spacing: 3px; color: var(--white);
  }
</style>
</head>
<body>
<main class="stage">

  <section class="card card-front" aria-label="Business card front">
    <svg viewBox="0 0 540 310" preserveAspectRatio="none" aria-hidden="true">
      <defs>
        <linearGradient id="bandFill" x1="0" y1="0" x2="1" y2="0">
          <stop offset="0" stop-color="#3b9bd6"/>
          <stop offset=".5" stop-color="#1a6fae"/>
          <stop offset="1" stop-color="#0f4f86"/>
        </linearGradient>
      </defs>
      <path d="M0,0 L80,0 Q25,18 0,70 Z" fill="url(#bandFill)"/>
      <path d="M95,0 Q28,22 6,88" fill="none" stroke="#f39a1e" stroke-width="3"/>
      <path d="M0,268 C160,300 390,258 540,180 L540,310 L0,310 Z" fill="url(#bandFill)"/>
      <path d="M0,258 C160,292 380,252 540,172" fill="none" stroke="#ffffff" stroke-width="4"/>
      <path d="M0,252 C150,286 370,246 540,166" fill="none" stroke="#f39a1e" stroke-width="6"/>
      <path d="M0,292 C170,310 400,280 540,230" fill="none" stroke="#3b9bd6" stroke-width="3" opacity=".6"/>
    </svg>

    <div class="brand-front">
      <span class="brand-dot" aria-hidden="true"></span>
      <span class="brand-name">MoneyMendPlus</span>
    </div>

    <ul class="contact">
      <li class="address">30871 Calloway Ln. B-22, Houston, TX 75419</li>
      <li><svg viewBox="0 0 10 10"><path d="M2,0 L4,0 L4.6,2.6 L3.4,3.6 Q4.5,5.8 6.4,6.6 L7.4,5.4 L10,6 L10,8 Q9,10 7,9.6 Q1,7.8 0,2 Q0,0 2,0 Z"/></svg>555-318-6207</li>
      <li><svg viewBox="0 0 10 10"><rect x="2" y="0" width="6" height="3"/><rect x="0" y="3.5" width="10" height="4" rx="1"/><rect x="2" y="7" width="6" height="3"/></svg>555-294-7153</li>
      <li><svg viewBox="0 0 10 10"><rect x="0" y="2" width="10" height="7" rx="1"/><path d="M0,2 L5,6 L10,2" stroke="#fff" fill="none"/></svg>info@miravelllending.example</li>
      <li><svg viewBox="0 0 10 10"><circle cx="5" cy="5" r="4.5"/><path d="M0.5,5 H9.5 M5,0.5 V9.5" stroke="#fff" stroke-width=".8"/></svg>www.miravelllending.example</li>
    </ul>

    <p class="slogan">Happiness<br>Restored!</p>
  </section>

  <section class="card card-back" aria-label="Business card back">
    <div class="back-frame" aria-hidden="true"></div>
    <p class="brand-back">MoneyMendPlus</p>
    <p class="back-company">Mira Vell Lending</p>
    <p class="back-web">www.miravelllending.example</p>
  </section>

</main>
</body>
</html>
```